Boutique custom software development company needs new business card

Our nearly 20 year old custom software development company would like to better include the fact that we are now providing Bitcoin services. These new services are B2B include education (how to acquire and securely hold Bitcoin) and integrating Bitcoin payments into existing ecommerce sites or other existing systems. Please keep the card clean and simple. Attached is our current design and some other files. vextorial.com

Target Market(s)

businesses owners interested in long term relationship

Industry/Entity Type

Custom software development and Bitcoin

Contact Information for Business Card

Dale Parker, dale@vextorial.com, vextorial.com, (888) 555-VXTRL

Font styles to use
Other font styles liked:
• monospace

Requirements
Must have
• double-sided
Nice to have
• clean and simple
Should not have
• physical address

```html
<!DOCTYPE html>
<html lang="en">
<head>
<meta charset="utf-8">
<title>Vextorial Business Card</title>
<link rel="stylesheet" href="https://fonts.googleapis.com/css2?family=Open+Sans:wght@400;700;800&family=Lato:wght@400&display=swap">
<style>
  :root {
    --orange: #f07f23;
    --blue: #3d76ba;
    --white: #ffffff;
    --ink: #1a1a1a;
    --stage: #000000;
  }
  * { margin: 0; padding: 0; box-sizing: border-box; }
  html, body { width: 1200px; height: 1200px; overflow: hidden; background: var(--stage); }
  .sheet { position: relative; width: 1200px; height: 1200px; }
  .card {
    position: absolute; left: 218px; width: 756px; height: 432px;
    border-radius: 36px; overflow: hidden;
  }
  .card--front { top: 142px; background: var(--orange); }
  .card--back { top: 619px; background: var(--white); }

  .brand {
    position: absolute; left: 0; right: 0; top: 118px; text-align: center;
    font-family: "Open Sans", sans-serif; font-weight: 800; font-size: 96px;
    line-height: 1.2; color: var(--blue); letter-spacing: 2px;
  }
  .brand__tagline {
    position: absolute; left: 0; right: 0; top: 252px; text-align: center;
    font-family: "Lato", sans-serif; font-size: 38px; line-height: 1.2;
    color: var(--blue); letter-spacing: -1.5px;
  }

  .mark { position: absolute; left: 99px; top: 196px; display: flex; align-items: center; gap: 12px; }
  .mark__square { width: 38px; height: 38px; background: var(--blue); }
  .mark__name {
    font-family: "Open Sans", sans-serif; font-weight: 700; font-size: 32px; line-height: 1; color: var(--blue);
  }
  .divider { position: absolute; left: 377px; top: 103px; width: 2px; height: 226px; background: var(--blue); }

  .contact { position: absolute; left: 432px; top: 117px; font-family: "Open Sans", sans-serif; color: var(--ink); }
  .contact__name { font-weight: 700; font-size: 31px; line-height: 1.2; letter-spacing: 0.5px; }
  .contact__first { color: var(--orange); }
  .contact__last { color: var(--blue); }
  .contact__services { margin-top: 10px; font-size: 20px; line-height: 26px; }
  .contact__list { list-style: none; margin-top: 14px; font-size: 20px; line-height: 25.5px; }
  .contact__list li { display: flex; align-items: center; gap: 10px; }
  .contact__list svg { width: 18px; height: 18px; flex: none; }

  .band { position: absolute; left: 0; bottom: 0; width: 756px; height: 28px; }
</style>
</head>
<body>
<main class="sheet">
  <section class="card card--front">
    <div class="brand">VEXTORIAL</div>
    <p class="brand__tagline">developer of custom applications</p>
  </section>

  <section class="card card--back">
    <div class="mark">
      <span class="mark__square"></span>
      <span class="mark__name">Vextorial</span>
    </div>
    <div class="divider"></div>
    <div class="contact">
      <h1 class="contact__name"><span class="contact__first">Dale</span> <span class="contact__last">Parker</span></h1>
      <p class="contact__services">Custom Software &amp;<br>Bitcoin Services</p>
      <ul class="contact__list">
        <li>
          <svg viewBox="0 0 24 24"><path fill="#f07f23" d="M6.6 10.8a15.1 15.1 0 0 0 6.6 6.6l2.2-2.2c.3-.3.7-.4 1-.2 1.1.4 2.3.6 3.6.6.6 0 1 .4 1 1V20c0 .6-.4 1-1 1A17 17 0 0 1 3 4c0-.6.4-1 1-1h3.5c.6 0 1 .4 1 1 0 1.3.2 2.5.6 3.6.1.3 0 .7-.2 1z"/><path fill="none" stroke="#f07f23" stroke-width="1.6" d="M14 2.5a8 8 0 0 1 7.5 7.5M14 6a4.5 4.5 0 0 1 4 4"/></svg>
          <span>(888) 555-VXTRL</span>
        </li>
        <li>
          <svg viewBox="0 0 24 24"><circle cx="12" cy="12" r="10" fill="#f07f23"/><path fill="none" stroke="#fff" stroke-width="1.4" d="M2 12h20M12 2c3 3 3 17 0 20M12 2c-3 3-3 17 0 20"/></svg>
          <span>www.vextorial.com</span>
        </li>
        <li>
          <svg viewBox="0 0 24 24"><path fill="#f07f23" d="M2 9l10 7 10-7v13H2z"/><path fill="none" stroke="#f07f23" stroke-width="1.6" d="M5 10V3h14v7"/><circle cx="12" cy="7.5" r="2.5" fill="none" stroke="#f07f23" stroke-width="1.4"/></svg>
          <span>dale@vextorial.com</span>
        </li>
      </ul>
    </div>
    <svg class="band" viewBox="0 0 756 28" preserveAspectRatio="none" aria-hidden="true">
      <polygon points="0,0 336,0 377,28 0,28" fill="#f07f23"/>
      <polygon points="364,0 756,0 756,28 405,28" fill="#3d76ba"/>
    </svg>
  </section>
</main>
</body>
</html>
```